Product Label with Company Logo & Product Information

I am looking for a new label design for one of my products, Candied Pecans. I am including an old label that I made, but it does not "pop" on the current packaging. See image of current packaging attached as well.

I want the design to ultimately be something that I can take and order a roll of labels/stickers. Please stick within standard label/sticker sizes (round or square). Please include final size as well.

Must Haves:
(1) Company logo (any color variation-see attached logo images).
(2) All wording on the old label
(3) Label size can not be more than 2 in. x 4 in. (I would actually like them a little smaller). They seem kind of big as they are right now.

```html
<!DOCTYPE html>
<html lang="en">
<head>
<meta charset="utf-8">
<title>Gourmet Candied Pecans Label</title>
<link href="https://fonts.googleapis.com/css2?family=Rye&family=Roboto:wght@700&display=swap" rel="stylesheet">
<style>
  :root {
    --stage: #222222;
    --honey: #f0e92a;
    --slate: #58585a;
    --paper: #ffffff;
  }
  html, body {
    margin: 0;
    padding: 0;
    width: 1200px;
    height: 780px;
    overflow: hidden;
    background: var(--stage);
  }
  .label {
    position: absolute;
    left: 40px;
    top: 40px;
    width: 1120px;
    height: 700px;
    box-sizing: border-box;
    border: 7px solid var(--honey);
    border-radius: 44px;
    background: var(--paper);
    overflow: hidden;
  }
  .label__waves {
    position: absolute;
    inset: 0;
    width: 100%;
    height: 100%;
  }
  .label__title {
    position: absolute;
    left: 60px;
    top: 70px;
    margin: 0;
    font-family: "Rye", serif;
    font-weight: 400;
    font-size: 74px;
    line-height: 1.05;
    letter-spacing: 1px;
  }
  .label__title-top {
    display: block;
    color: var(--honey);
    -webkit-text-stroke: 2px var(--slate);
  }
  .label__title-bottom {
    display: block;
    margin-left: 40px;
    color: var(--slate);
    -webkit-text-stroke: 1px var(--honey);
  }
  .brand {
    position: absolute;
    right: 80px;
    top: 80px;
    display: flex;
    align-items: center;
    gap: 18px;
  }
  .brand__mark {
    width: 46px;
    height: 46px;
    background: var(--slate);
  }
  .brand__name {
    font-family: "Rye", serif;
    font-size: 58px;
    color: var(--honey);
  }
  .details {
    position: absolute;
    left: 80px;
    bottom: 60px;
    margin: 0;
    font-family: "Rye", serif;
    font-size: 32px;
    line-height: 1.45;
    color: var(--honey);
  }
  .details__line { display: block; }
  .details__line--indent { padding-left: 24px; }
  .details__line--indent-more { padding-left: 48px; }
  .contact {
    position: absolute;
    right: 70px;
    top: 355px;
    display: flex;
    align-items: center;
    gap: 18px;
  }
  .contact__icon { width: 58px; height: 52px; }
  .contact__phone {
    font-family: "Roboto", sans-serif;
    font-weight: 700;
    font-size: 46px;
    color: var(--honey);
    letter-spacing: 1px;
  }
</style>
</head>
<body>
  <main class="label">
    <svg class="label__waves" viewBox="0 0 1106 686" preserveAspectRatio="none" aria-hidden="true">
      <path d="M0,420 C260,330 560,290 1106,250 L1106,300 C620,320 300,360 0,480 Z" fill="var(--slate)"/>
      <path d="M0,470 C300,360 640,330 1106,290 L1106,330 C660,350 320,380 0,500 Z" fill="var(--honey)"/>
      <path d="M0,500 C320,390 680,350 1106,330 L1106,686 L0,686 Z" fill="var(--slate)"/>
    </svg>

    <h1 class="label__title">
      <span class="label__title-top">GOURMET</span>
      <span class="label__title-bottom">CANDIED PECANS</span>
    </h1>

    <div class="brand">
      <span class="brand__mark"></span>
      <span class="brand__name">Meadow Hive</span>
    </div>

    <div class="contact">
      <svg class="contact__icon" viewBox="0 0 58 52" aria-hidden="true">
        <polygon points="14,2 44,2 57,26 44,50 14,50 1,26" fill="var(--honey)"/>
        <path d="M20,16 c3,-3 6,-3 8,0 l2,4 c1,2 0,3 -2,4 c1,3 4,6 7,7 c1,-2 2,-3 4,-2 l4,2 c3,2 3,5 0,8 c-4,3 -10,1 -16,-5 c-6,-6 -9,-13 -7,-18 z" fill="var(--slate)"/>
      </svg>
      <span class="contact__phone">(555)014-2780</span>
    </div>

    <p class="details">
      <span class="details__line">Made with Cinnamon</span>
      <span class="details__line details__line--indent">Brown Sugar &amp; Salt Order More</span>
      <span class="details__line details__line--indent-more">Meadow Hive Market, LLC</span>
    </p>
  </main>
</body>
</html>
```